Redesign This Psychology Website

We would like a slight redesign of this successful psychology (relationship counselling) website:

www.TheKelvaleClinic.com.au

We are updating the website, and we'd like a slight refresh of the design and style.

Please keep to very similar colours, and use the same logo. We're looking for around 10 page templates, however the main one is the home page.

Keep in mind, this website already converts quite well, so we want a new, fresh design in keeping with this one. Please don't bother designing something too extremely different.

thanks :)

Target Market(s)

couples who are looking for relationship counselling. Men and women, 25 - 70, across Australia

Industry/Entity Type

Psychology

Number of Pages Required

5+ page

Font styles to use
Sans Serif

Colors
87cfc6
b7a5cd
ec1f27
ffffff
cee9f5

Requirements
Must have
• a similar look to the current design, just looking for a slight refresh.
• Search bar
• Areas for lots of photos
• same logo
• lots of content areas
Nice to have
• great content areas, where we can display a lot of content and our areas.
Should not have
• no colors like orange, etc.
• should not have a totally different feel.

```html
<!DOCTYPE html>
<html lang="en">
<head>
<meta charset="utf-8">
<title>The Kelvale Clinic – Relationship Counselling</title>
<link href="https://fonts.googleapis.com/css2?family=Montserrat:wght@400;500;600;700&family=Open+Sans:wght@400;600;700&display=swap" rel="stylesheet">
<style>
:root{
  --teal:#87cfc6;
  --teal-dark:#5dbdb2;
  --lilac:#b7a5cd;
  --lilac-soft:#d6cbe4;
  --red:#ec1f27;
  --white:#ffffff;
  --sky:#cee9f5;
  --sky-deep:#b9dff0;
  --ink:#333333;
  --muted:#555555;
  --nav-text:#2d6f8f;
  --link-blue:#2a7fc0;
  --card-bg:#fbfafd;
  --line:#d9d9d9;
  --photo-a:#9fb8c8;
  --photo-b:#c9bcdc;
  --photo-c:#a7d8d1;
  --photo-d:#e6e1ee;
}
*{box-sizing:border-box;margin:0;padding:0}
html,body{width:1200px;height:3010px;overflow:hidden}
body{position:relative;background:var(--white);font-family:"Open Sans",Arial,sans-serif;color:var(--ink)}
.abs{position:absolute}

/* header */
.brand{left:100px;top:20px;display:flex;align-items:center;gap:12px}
.brand-mark{width:50px;height:50px;border-radius:50%;background:var(--teal-dark)}
.brand-name{font-family:"Montserrat",sans-serif;font-weight:600;font-size:26px;color:var(--teal-dark);line-height:1}
.brand-tag{left:164px;top:78px;font-family:"Montserrat",sans-serif;font-size:13px;color:var(--teal-dark)}
.socials{display:flex;gap:6px}
.socials span{width:28px;height:28px;border-radius:50%;display:block}
.s1{background:#3b5a9a}.s2{background:#2aa9e0}.s3{background:#d42a24}.s4{background:#8a7f9c}
.top-socials{left:688px;top:16px}
.call{left:848px;top:20px;display:flex;align-items:center;gap:10px;font-family:"Montserrat",sans-serif;font-weight:600;font-size:15px;color:var(--nav-text);letter-spacing:.3px}
.top-links{left:572px;top:68px;display:flex;align-items:center;font-family:"Montserrat",sans-serif;font-size:10px;color:var(--nav-text)}
.top-links .pill{background:var(--sky);padding:5px 8px;margin-right:10px}
.top-links .sep{margin:0 8px;color:#999}

.nav{left:0;top:112px;width:1200px;height:52px;background:var(--sky);display:flex;align-items:center}
.nav a{font-family:"Montserrat",sans-serif;font-size:14px;color:var(--nav-text);text-decoration:none;margin-left:32px}
.nav a:first-child{margin-left:128px}
.search{left:886px;top:121px;width:212px;height:32px;background:var(--white);display:flex;align-items:center;justify-content:space-between;padding:0 12px;font-size:11px;color:#666}
.subnav{left:0;top:168px;width:1200px;height:40px;background:var(--lilac);display:flex;align-items:center}
.subnav a{font-family:"Montserrat",sans-serif;font-size:13px;color:var(--white);text-decoration:none;margin-left:46px}
.subnav a:first-child{margin-left:136px}

/* hero */
.hero{left:0;top:210px;width:1200px;height:512px;background:
  radial-gradient(circle at 32% 45%,rgba(255,255,255,.45),rgba(255,255,255,0) 40%),
  linear-gradient(100deg,#a897bf 0%,#cdbfe0 35%,#dff0f7 62%,#9fd6cf 100%)}
.hero-arrows{left:124px;top:606px;display:flex;gap:4px}
.hero-arrows span{width:22px;height:22px;background:rgba(255,255,255,.85);display:flex;align-items:center;justify-content:center}
.video{left:606px;top:346px;width:492px;height:276px;background:linear-gradient(#ffffff,#e7eef3);box-shadow:0 2px 6px rgba(0,0,0,.3)}
.video-play{position:absolute;left:50%;top:46%;transform:translate(-50%,-50%);width:64px;height:64px;border-radius:50%;background:var(--teal);display:flex;align-items:center;justify-content:center}
.video-bar{position:absolute;left:0;bottom:0;width:100%;height:30px;background:#1c1c1c;display:flex;align-items:center;padding:0 12px;gap:14px;color:#fff;font-size:11px}
.video-progress{position:absolute;left:0;bottom:30px;height:3px;width:100%;background:#555}
.video-progress i{display:block;width:4%;height:100%;background:var(--red)}

/* service cards */
.cards{left:100px;top:666px;display:flex;gap:10px}
.card{width:242px;height:414px;background:var(--card-bg);border:1px solid #e6e1ee;position:relative}
.card-photo{height:198px;width:100%}
.card h3{font-family:"Montserrat",sans-serif;font-weight:500;font-size:16px;line-height:22px;color:var(--link-blue);margin:12px 14px 4px}
.card h4{font-size:12px;font-weight:700;color:var(--link-blue);margin:0 14px 10px}
.card p{font-size:12px;line-height:22px;color:var(--muted);margin:0 14px;text-align:justify}
.btn-lilac{position:absolute;left:14px;bottom:20px;background:var(--lilac);color:#fff;font-size:11px;padding:7px 10px}

/* finder */
.finder{left:102px;top:1126px;width:994px;height:184px;background:linear-gradient(var(--lilac),#c8b9da);box-shadow:0 3px 8px rgba(0,0,0,.15)}
.finder h2{position:absolute;top:34px;width:100%;text-align:center;font-family:"Montserrat",sans-serif;font-weight:400;font-size:24px;color:#fff}
.finder-row{position:absolute;left:114px;top:90px;display:flex;gap:22px}
.field{width:202px;height:34px;background:#fff;font-size:11px;color:#888;display:flex;align-items:center;padding:0 14px}
.btn-red{width:98px;height:34px;background:var(--red);color:#fff;font-size:12px;font-weight:700;display:flex;align-items:center;justify-content:center}

/* specialise */
.about{left:128px;top:1346px;width:510px}
.about h2{font-family:"Montserrat",sans-serif;font-weight:600;font-size:24px;line-height:30px;color:var(--teal)}
.about p{font-size:13px;line-height:24px;color:#444;margin-top:14px}
.btn-teal{display:inline-block;background:var(--teal);color:#fff;font-size:11px;padding:7px 10px;margin-top:14px}
.about-photo{left:676px;top:1360px;width:388px;height:310px;border:6px solid #fff;box-shadow:0 2px 8px rgba(0,0,0,.25);background:
  radial-gradient(circle at 60% 40%,rgba(255,255,255,.35),rgba(255,255,255,0) 45%),
  linear-gradient(120deg,#8fa6bb,#c9bcdc 55%,#7f95ad)}

/* section headings */
.sec-title{font-family:"Montserrat",sans-serif;font-weight:600;font-size:24px;color:var(--teal)}
.sec-line{height:1px;background:var(--line)}
.pager{display:flex;gap:4px}
.pager span{width:20px;height:20px;background:#eee;display:flex;align-items:center;justify-content:center}
.thumbs{left:128px;top:1794px;display:flex;gap:24px}
.thumb{width:216px;height:152px;box-shadow:0 2px 6px rgba(0,0,0,.25)}

/* blog */
.blog-sub{left:124px;top:2022px;font-family:"Montserrat",sans-serif;font-size:15px;color:#444}
.posts{left:126px;top:2064px;display:flex;gap:38px}
.post{width:290px;height:468px;background:#f5f5f5;position:relative;box-shadow:0 1px 4px rgba(0,0,0,.12)}
.post-photo{height:218px;margin:6px 6px 0}
.date{position:absolute;left:6px;top:6px;width:62px;height:88px;background:#fff;text-align:center;font-family:"Montserrat",sans-serif;font-weight:700;color:#333;padding-top:6px}
.date b{display:block;font-size:30px;line-height:32px}
.date i{display:block;font-style:normal;font-size:18px;line-height:20px}
.date s{display:block;text-decoration:none;font-size:11px;font-weight:500}
.post h3{font-size:14px;font-weight:700;text-align:center;margin:16px 20px 0;line-height:20px;color:#222}
.post p{font-size:11.5px;text-align:center;line-height:24px;color:#555;margin:14px 18px 0}
.post .btn-teal{position:absolute;left:50%;transform:translateX(-50%);bottom:24px;margin:0}

/* footer */
.footer{left:0;top:2640px;width:1200px;height:324px;background:var(--sky)}
.login{left:102px;top:2588px;width:994px;height:102px;background:var(--red);box-shadow:0 3px 8px rgba(0,0,0,.2);display:flex;align-items:center}
.login h2{font-family:"Montserrat",sans-serif;font-weight:600;font-size:21px;color:#fff;margin:0 22px 0 88px}
.login .field{width:242px;height:38px;margin-right:6px}
.login .submit{width:118px;height:38px;background:var(--teal);color:#fff;font-size:13px;font-weight:700;display:flex;align-items:center;justify-content:center}
.quick-title{left:134px;top:2734px;font-family:"Montserrat",sans-serif;font-weight:600;font-size:20px;color:#333}
.quick{left:136px;top:2776px;display:flex}
.quick ul{list-style:none}
.quick li{font-size:13px;line-height:26px;color:#333}
.quick li::before{content:"›";margin-right:14px;color:#555}
.col1{width:164px}.col2{width:326px}.col3{width:300px}
.foot-brand{left:942px;top:2750px;width:132px;display:flex;flex-direction:column;align-items:center;gap:10px}
.foot-brand .mark{width:52px;height:52px;border-radius:50%;background:var(--teal-dark)}
.foot-brand .name{font-family:"Montserrat",sans-serif;font-weight:600;font-size:13px;color:var(--teal-dark);white-space:nowrap}
.bottom-bar{left:0;top:2964px;width:1200px;height:46px;background:var(--sky-deep);display:flex;align-items:center;justify-content:center;font-size:11px;color:#555}
</style>
</head>
<body>

<header>
  <div class="abs brand"><span class="brand-mark"></span><span class="brand-name">The Kelvale Clinic</span></div>
  <div class="abs brand-tag">helping you create loving relationships</div>
  <div class="abs socials top-socials"><span class="s1"></span><span class="s2"></span><span class="s3"></span><span class="s4"></span></div>
  <div class="abs call">
    <svg width="16" height="16" viewBox="0 0 24 24"><path fill="#2d6f8f" d="M6.6 10.8a15 15 0 0 0 6.6 6.6l2.2-2.2c.3-.3.7-.4 1-.2 1.1.4 2.3.6 3.6.6.6 0 1 .4 1 1V20c0 .6-.4 1-1 1A17 17 0 0 1 3 4c0-.6.4-1 1-1h3.5c.6 0 1 .4 1 1 0 1.3.2 2.5.6 3.6.1.3 0 .7-.2 1z"/></svg>
    CALL US ON : 1-300 555 014
  </div>
  <div class="abs top-links"><span class="pill">JOIN OUR ASSOCIATE PROGRAM</span>MARRIAGE COUNSELLING<span class="sep">|</span>RELATIONSHIP COUNSELLING</div>

  <nav class="abs nav"><a>Home</a><a>About</a><a>Resources</a><a>Blog</a><a>Shop</a><a>Cart</a></nav>
  <div class="abs search">Search
    <svg width="16" height="16" viewBox="0 0 24 24"><circle cx="10" cy="10" r="6.5" fill="none" stroke="#2d6f8f" stroke-width="3"/><path d="M15 15l6 6" stroke="#2d6f8f" stroke-width="3"/></svg>
  </div>
  <nav class="abs subnav"><a>Counselling Types</a><a>Relationship Counselling Locations</a><a>Sex Theraphy Locations</a><a>Quizzes</a><a>F.A. Q ' s</a><a>Contact Us</a></nav>
</header>

<section>
  <div class="abs hero" role="img" aria-label="Photo of a couple sitting in a sunlit field with a guitar"></div>
  <div class="abs hero-arrows">
    <span><svg width="8" height="10"><path d="M7 0L1 5l6 5" fill="none" stroke="#333" stroke-width="1.5"/></svg></span>
    <span><svg width="8" height="10"><path d="M1 0l6 5-6 5" fill="none" stroke="#333" stroke-width="1.5"/></svg></span>
  </div>
  <div class="abs video" role="img" aria-label="Introductory video player">
    <div class="video-play"><svg width="22" height="24"><path d="M2 0l20 12L2 24z" fill="#fff"/></svg></div>
    <div class="video-progress"><i></i></div>
    <div class="video-bar">
      <svg width="10" height="12"><path d="M0 0l10 6-10 6z" fill="#fff"/></svg>
      <svg width="14" height="12"><path d="M0 4h4l5-4v12l-5-4H0z" fill="#fff"/></svg>
      <span>0:01 / 4:29</span>
    </div>
  </div>

  <div class="abs cards">
    <article class="card">
      <div class="card-photo" role="img" aria-label="Black and white photo of a woman sitting alone" style="background:linear-gradient(135deg,#8e9298,#d9dbde)"></div>
      <h3>Relationship Counselling</h3><h4>Do you need help with:</h4>
      <p>Communication, Recovering from an affair, Loss of intimacy &amp; love, Power battles, Feeling like friends, not lovers</p>
      <span class="btn-lilac">Read more</span>
    </article>
    <article class="card">
      <div class="card-photo" role="img" aria-label="Photo of a couple embracing by the sea" style="background:linear-gradient(135deg,#a9c9d6,#dde9ee 60%,#c3b6d6)"></div>
      <h3>Sex Theraphy Counselling</h3><h4>Do you need help with:</h4>
      <p>Low libido , Erectile difficulties, Premature ejaculation, Differing libidos, Porn addiction, Keeping sex exciting</p>
      <span class="btn-lilac">Read more</span>
    </article>
    <article class="card">
      <div class="card-photo" role="img" aria-label="Photo of a couple in conflict on a bed" style="background:linear-gradient(135deg,#eef2f4,#b9c6d0)"></div>
      <h3>Anger Management Counselling</h3><h4>Do you need help with:</h4>
      <p>Managing angry outbursts, expressing your anger in healthy ways</p>
      <span class="btn-lilac">Read more</span>
    </article>
    <article class="card">
      <div class="card-photo" role="img" aria-label="Photo of a woman reading a card" style="background:linear-gradient(135deg,#d6cbe4,#f1eef6)"></div>
      <h3>Narcissism Counselling</h3><h4>Do you need help with:</h4>
      <p>Managing narcissistic, superior, entitled, arrogant and lack of empathy tendencies in you or your partner</p>
      <span class="btn-lilac">Read more</span>
    </article>
  </div>
</section>

<section class="abs finder">
  <h2>Find Our Psychologist Near You</h2>
  <div class="finder-row">
    <div class="field">Type of Counselling</div><div class="field">Location</div><div class="field">Postcode</div>
    <div class="btn-red">Search</div>
  </div>
</section>

<section>
  <div class="abs about">
    <h2>We Specialise in Relationship &amp;<br>Marriage Counselling</h2>
    <p>At the Kelvale Clinic, we are a group of PSYCHOLOGISTS, Australia wide who are passionate about relationships and helping you with yours.</p>
    <p>Our vision is to provide the most highly regarded and comprehensive marriage counselling and relationship counselling, and sex therapy in Australia, at reasonable and affordable rates.</p>
    <p>When we are experiencing relationship and marriage problems, there can be a lot of pain and confusion, and it can often be difficult to cope with the other areas of our lives when we are struggling with problems with our partner.</p>
    <span class="btn-teal">Read more</span>
  </div>
  <div class="abs about-photo" role="img" aria-label="Photo of a laughing couple close together"></div>
</section>

<section>
  <h2 class="abs sec-title" style="left:126px;top:1732px">Photos and Videos</h2>
  <div class="abs sec-line" style="left:366px;top:1750px;width:650px"></div>
  <div class="abs pager" style="left:1024px;top:1752px">
    <span><svg width="6" height="8"><path d="M5 0L1 4l4 4" fill="none" stroke="#333" stroke-width="1.3"/></svg></span>
    <span><svg width="6" height="8"><path d="M1 0l4 4-4 4" fill="none" stroke="#333" stroke-width="1.3"/></svg></span>
  </div>
  <div class="abs thumbs">
    <div class="thumb" role="img" aria-label="Photo of a couple at sunset" style="background:linear-gradient(135deg,#c9bcdc,#9fb8c8)"></div>
    <div class="thumb" role="img" aria-label="Photo of a couple by a stone wall" style="background:linear-gradient(135deg,#b8bfc6,#7d8a96)"></div>
    <div class="thumb" role="img" aria-label="Video still of a woman by a chalkboard drawing" style="background:linear-gradient(135deg,#3f4650,#5c6570)"></div>
    <div class="thumb" role="img" aria-label="Photo of a couple lying together" style="background:linear-gradient(135deg,#e6e1ee,#a7d8d1)"></div>
  </div>
</section>

<section>
  <h2 class="abs sec-title" style="left:126px;top:1990px">Blog</h2>
  <div class="abs blog-sub">Relationships &amp; Sex</div>
  <div class="abs sec-line" style="left:282px;top:2032px;width:734px"></div>
  <div class="abs pager" style="left:1024px;top:2006px">
    <span><svg width="6" height="8"><path d="M5 0L1 4l4 4" fill="none" stroke="#333" stroke-width="1.3"/></svg></span>
    <span><svg width="6" height="8"><path d="M1 0l4 4-4 4" fill="none" stroke="#333" stroke-width="1.3"/></svg></span>
  </div>
  <div class="abs posts">
    <article class="post">
      <div class="post-photo" role="img" aria-label="Photo of two smiling men" style="background:linear-gradient(135deg,#a7d8d1,#c9d8c4 60%,#9fb8c8)"></div>
      <div class="date"><b>05</b><i>FEB</i><s>2017</s></div>
      <h3>Duis aute irure dolor in reprehenderit in voluptate</h3>
      <p>Duis aute irure dolor in reprehenderit in voluptate velit esse cillum dolore eu fugiat nulla pariatur. Excepteur sint occaecat cupidatat ...</p>
      <span class="btn-teal">Read more</span>
    </article>
    <article class="post">
      <div class="post-photo" role="img" aria-label="Photo of a couple hugging in winter clothes" style="background:linear-gradient(135deg,#b9c6d0,#d6cbe4 55%,#c7727a)"></div>
      <div class="date"><b>05</b><i>FEB</i><s>2017</s></div>
      <h3>Duis aute irure dolor in reprehenderit in voluptate</h3>
      <p>Duis aute irure dolor in reprehenderit in voluptate velit esse cillum dolore eu fugiat nulla pariatur. Excepteur sint occaecat cupidatat ...</p>
      <span class="btn-teal">Read more</span>
    </article>
    <article class="post">
      <div class="post-photo" role="img" aria-label="Photo of two women outdoors" style="background:linear-gradient(135deg,#f1eef6,#cee9f5 50%,#b7a5cd)"></div>
      <div class="date"><b>05</b><i>FEB</i><s>2017</s></div>
      <h3>Duis aute irure dolor in reprehenderit in voluptate</h3>
      <p>Duis aute irure dolor in reprehenderit in voluptate velit esse cillum dolore eu fugiat nulla pariatur. Excepteur sint occaecat cupidatat ...</p>
      <span class="btn-teal">Read more</span>
    </article>
  </div>
</section>

<footer>
  <div class="abs footer"></div>
  <div class="abs login">
    <h2>Member Login</h2>
    <div class="field">Email</div><div class="field">Password</div>
    <div class="submit">Submit</div>
  </div>
  <h2 class="abs quick-title">Quick Links</h2>
  <div class="abs quick">
    <ul class="col1"><li>Home</li><li>About Us</li><li>Resources</li><li>Blog</li><li>Shop</li><li>Cart</li></ul>
    <ul class="col2"><li>Counselling Types</li><li>Relationship Counselling Locations</li><li>Sex Theraphy Locations</li><li>Quizzes</li><li>F.A. Q ' s</li><li>Contact Us</li></ul>
    <ul class="col3"><li>Privacy Policy</li><li>Terms &amp; Conditions</li><li>Site Map</li><li>Associate Psychologists Program</li></ul>
  </div>
  <div class="abs foot-brand">
    <span class="mark"></span>
    <span class="name">The Kelvale Clinic</span>
    <div class="socials"><span class="s1"></span><span class="s2"></span><span class="s3"></span><span class="s4"></span></div>
  </div>
  <div class="abs bottom-bar">Copyrights © 2017, www.kelvaleclinic.example. All Rights Reserved.</div>
</footer>

</body>
</html>
```